Workshop PPT Update for AI Transformation Sessions

Our strategic consulting firm runs strategy workshops using slides as workshop exercises. These slides are used to communicate to the participants in advance, run the workshops and produce the final deliverable.

It is time for a design "upgrade". We'd like them to be more engaging, hipper and more interesting. These slides are utilitarian, so clean and usable is good. I have attached the example of what we have today. I have also attached an example of another company's slides that I like.

We can't rip off their design nor can we go away 100% from what we have. But I think it is possible to "update" our look to something closer to their look. Grey colors are fine with some color pop.

Slide styles needed are - 1) Cover Page, 2) Instructions Page, 3) Bullet list 4) Worksheet (place for participants to add content 5) Table, 6) Two column.

```html
<!DOCTYPE html>
<html lang="en">
<head>
<meta charset="utf-8">
<title>Northpath Strategy – Kickoff &amp; Discovery</title>
<link href="https://fonts.googleapis.com/css2?family=Montserrat:wght@500;600;700&family=Nunito+Sans:wght@400;600;700&display=swap" rel="stylesheet">
<style>
  :root {
    --canvas: #d4d4d5;
    --slate: #434653;
    --brick: #a8413c;
    --ink: #28222f;
    --paper: #ffffff;
    --panel: #f6f6f7;
    --cell: #eeeeef;
    --text: #2b2b33;
    --muted: #4a4a52;
    --soft: #d2d2d7;
  }
  * { box-sizing: border-box; margin: 0; padding: 0; }
  html, body { width: 1200px; height: 4057px; overflow: hidden; }
  body {
    background: var(--canvas);
    position: relative;
    font-family: "Nunito Sans", Arial, sans-serif;
    color: var(--text);
  }
  .slide {
    position: absolute;
    left: 83px;
    width: 1033px;
    height: 581px;
    overflow: hidden;
  }
  .abs { position: absolute; }
  .display { font-family: "Montserrat", Arial, sans-serif; font-weight: 600; }
  .page-no { position: absolute; font-size: 16px; }

  /* Cover */
  .cover { top: 93px; background: var(--slate); }
  .cover .brand { top: 168px; width: 100%; text-align: center; font-size: 78px; color: #fff; font-weight: 500; letter-spacing: -1px; line-height: 1; }
  .cover .title { top: 322px; width: 100%; text-align: center; font-size: 64px; color: var(--soft); line-height: 1; }
  .cover .rule { top: 406px; left: 332px; width: 370px; height: 1px; background: #8d8f99; }
  .cover .subtitle { top: 420px; width: 100%; text-align: center; font-size: 29px; color: #e6e6ea; font-weight: 400; }

  /* Getting started */
  .start { top: 754px; background: var(--brick); }
  .start .sheet { left: 19px; top: 17px; width: 698px; height: 548px; background: var(--panel); }
  .start .side { left: 736px; top: 0; width: 297px; height: 581px; background: var(--slate); }
  .start .side-title { left: 0; top: 226px; width: 297px; text-align: center; font-size: 50px; color: #fff; line-height: 1.08; }
  .start .side-rule { left: 47px; top: 345px; width: 205px; height: 1px; background: #9a9ca6; }
  .start .steps { left: 88px; top: 196px; list-style: none; }
  .start .steps li { display: flex; align-items: center; height: 51px; font-size: 26px; color: var(--muted); }
  .start .steps svg { width: 26px; height: 26px; margin-right: 28px; flex: none; }
  .start .page-no { right: 20px; top: 540px; color: #fff; }

  /* Two-panel frame (overview / principles) */
  .split { background: var(--slate); }
  .split .rail { left: 0; top: 0; width: 306px; height: 581px; background: var(--brick); color: #fff; }
  .split .rail-title { left: 0; top: 24px; width: 306px; text-align: center; font-size: 48px; line-height: 1.14; }
  .split .rail-rule { left: 62px; top: 140px; width: 204px; height: 1px; background: #d8a4a1; }
  .split .board { left: 326px; top: 16px; width: 690px; height: 548px; background: var(--panel); }
  .split .page-no { right: 28px; top: 539px; color: var(--brick); }

  .overview { top: 1417px; }
  .overview .meta { left: 15px; top: 198px; width: 285px; font-size: 21px; line-height: 1.4; }
  .overview .prep-title { left: 15px; top: 278px; font-size: 30px; font-weight: 700; }
  .overview .prep { left: 15px; top: 326px; list-style: none; font-size: 21px; }
  .overview .prep li { height: 36px; }
  .flow-title { left: 38px; top: 46px; font-size: 36px; font-weight: 500; color: var(--ink); }
  .flow { left: 38px; top: 106px; width: 630px; }
  .flow h3 { font-family: "Montserrat", Arial, sans-serif; font-size: 21px; font-weight: 700; margin-top: 10px; color: var(--ink); }
  .flow h3.accent { color: var(--brick); }
  .flow p { font-size: 18px; color: var(--muted); line-height: 1.55; margin-top: 2px; }

  /* Instructions */
  .instructions { top: 2079px; background: var(--paper); }
  .band { left: 0; top: 0; width: 1033px; height: 66px; text-align: center; color: #fff; font-size: 46px; line-height: 66px; }
  .instructions .band { background: var(--brick); }
  .instructions .aside { left: 654px; top: 66px; width: 379px; height: 515px; background: var(--ink); color: #fff; }
  .instructions .body { left: 49px; top: 106px; width: 580px; }
  .instructions .purpose { font-size: 21px; line-height: 1.4; }
  .instructions .label { font-size: 23px; font-weight: 700; margin-top: 12px; }
  .instructions ol { list-style: none; margin-top: 6px; }
  .instructions li { font-family: "Montserrat", Arial, sans-serif; font-size: 20px; font-weight: 700; margin-top: 13px; color: var(--ink); }
  .instructions li.accent { color: var(--brick); }
  .instructions li span { display: block; font-family: "Nunito Sans", Arial, sans-serif; font-weight: 400; font-size: 18px; color: var(--muted); margin: 6px 0 0 25px; }
  .aside-inner { left: 31px; top: 68px; width: 330px; }
  .aside h4 { font-family: "Montserrat", Arial, sans-serif; font-size: 23px; font-weight: 600; margin-bottom: 14px; }
  .aside ul { list-style: none; font-size: 19px; margin-bottom: 26px; }
  .aside ul li { height: 35px; }
  .aside p { font-size: 19px; margin-bottom: 28px; }
  .instructions .page-no { right: 28px; top: 538px; color: #fff; }

  /* Principles worksheet */
  .principles { top: 2740px; }
  .principles .lead { left: 28px; top: 242px; width: 260px; font-size: 21px; line-height: 1.45; }
  .timeline { left: 74px; top: 80px; width: 2px; height: 400px; border-left: 2px dashed #b9b9c0; }
  .principle { left: 36px; width: 630px; height: 76px; display: flex; }
  .principle .mark { width: 76px; height: 76px; flex: none; display: flex; align-items: center; justify-content: center; }
  .principle .mark.dark { background: var(--ink); }
  .principle .mark.red { background: var(--brick); }
  .principle .copy { margin-left: 28px; padding-top: 0; }
  .principle h3 { font-family: "Montserrat", Arial, sans-serif; font-size: 21px; font-weight: 700; color: var(--ink); margin-top: -22px; }
  .principle h3.accent { color: var(--brick); }
  .principle p { font-size: 15px; line-height: 1.4; color: var(--muted); margin-top: 6px; }

  /* Table */
  .structure { top: 3402px; background: var(--paper); }
  .structure .band { background: var(--ink); }
  .plan { position: absolute; left: 28px; top: 106px; width: 975px; border-collapse: separate; border-spacing: 15px 0; margin-left: -15px; font-size: 18px; }
  .plan th { height: 48px; color: #fff; font-weight: 500; font-size: 18px; }
  .plan th.red { background: var(--brick); }
  .plan th.dark { background: var(--ink); }
  .plan td { text-align: center; color: var(--text); line-height: 1.55; }
  .plan td.level { text-align: left; padding-left: 10px; }
  .plan tr.shade td { background: var(--cell); }
  .plan .gap td { height: 0; }
  .structure .page-no { right: 28px; top: 542px; color: var(--brick); }
</style>
</head>
<body>

<section class="slide cover">
  <div class="abs brand">Northpath Strategy</div>
  <h1 class="abs display title">Kickoff &amp; Discovery</h1>
  <div class="abs rule"></div>
  <p class="abs subtitle">Sizing &amp; Scoping AI Transformation</p>
</section>

<section class="slide start">
  <div class="abs sheet">
    <ul class="abs steps">
      <li><svg viewBox="0 0 24 24"><path d="M22 2 L2 10 L11 13 L14 22 Z" fill="#a8413c"/></svg>Complete the Engagement Sizing Survey.</li>
      <li><svg viewBox="0 0 24 24"><path d="M22 2 L2 10 L11 13 L14 22 Z" fill="#434653"/></svg>Collect relevant inputs.</li>
      <li><svg viewBox="0 0 24 24"><path d="M22 2 L2 10 L11 13 L14 22 Z" fill="#a8413c"/></svg>Determine workshop participants &amp; date.</li>
      <li><svg viewBox="0 0 24 24"><path d="M22 2 L2 10 L11 13 L14 22 Z" fill="#434653"/></svg>Send invites, to include pre-work.</li>
    </ul>
  </div>
  <div class="abs side">
    <h2 class="abs display side-title">Getting<br>Started</h2>
    <div class="abs side-rule"></div>
    <span class="page-no">| Page 2</span>
  </div>
</section>

<section class="slide split overview">
  <div class="abs rail">
    <h2 class="abs display rail-title">Workshop<br>Overview</h2>
    <div class="abs rail-rule"></div>
    <p class="abs meta">Participants: Execs Duration: 2 hrs.</p>
    <h3 class="abs display prep-title">Prep Work:</h3>
    <ul class="abs prep">
      <li>-&nbsp;&nbsp; Org Strategy</li>
      <li>-&nbsp; 2023 Goal Performance</li>
      <li>-&nbsp; Existing policies</li>
      <li>-&nbsp; Pre-thinking questions</li>
    </ul>
  </div>
  <div class="abs board">
    <h2 class="abs flow-title">Workshop Flow</h2>
    <div class="abs flow">
      <h3 class="accent">Confirm Company Direction</h3>
      <p>Recap organizational purpose, values, vision &amp; winning strategy.</p>
      <h3>Develop AI Vision</h3>
      <h3 class="accent">Develop AI Guiding Principles</h3>
      <p>Developed AI Guiding Principles, supporting policies to include approved tools.</p>
      <h3>Agree on a Governance Approach</h3>
      <p>Agreed upon governance approach, structure, &amp; executive champion.</p>
      <h3 class="accent">Agree on a Training &amp; Learning Approach</h3>
      <p>Set approach to training &amp; continuous learning. tools.</p>
      <h3>Determine Rollout &amp; Communication</h3>
      <p>Organizational rollout &amp; continuous communication.</p>
    </div>
    <span class="page-no">| Page 3</span>
  </div>
</section>

<section class="slide instructions">
  <h2 class="abs display band">Creating your AI Guiding Principles</h2>
  <div class="abs body">
    <p class="purpose">Purpose: To create behavioral statements that everyone is expected to adhere to.</p>
    <p class="label">Instructions:</p>
    <ol>
      <li class="accent">1. Create the Outline.<span>Determine the topics that need a principle.</span></li>
      <li>2. Audit the Outline.<span>Look at the current policies to determine if all topics are covered.</span></li>
      <li class="accent">3. Draft the Guiding Principles.</li>
      <li>4. Determine which GPs need detailed policies.</li>
      <li class="accent">5. Determine which AI Tools support the GPs.</li>
      <li>6. Finalize via a legal and executive review.</li>
    </ol>
  </div>
  <aside class="abs aside">
    <div class="abs aside-inner">
      <h4>Your Existing Material:</h4>
      <ul>
        <li>-&nbsp; Company Values</li>
        <li>-&nbsp; Current Policies (GDPR, CCPA, etc.)</li>
        <li>-&nbsp; Legal Guidance</li>
        <li>-&nbsp; Other</li>
      </ul>
      <h4>Examples for Inspiration</h4>
      <p>See next slides</p>
      <h4>PromptPal Prompts</h4>
      <p>HERE</p>
    </div>
    <span class="page-no">| Page 4</span>
  </aside>
</section>

<section class="slide split principles">
  <div class="abs rail">
    <h2 class="abs display rail-title">AI Guiding<br>Principles</h2>
    <div class="abs rail-rule"></div>
    <p class="abs lead">What guides our decision making and approach?</p>
  </div>
  <div class="abs board">
    <div class="abs timeline"></div>
    <div class="abs principle" style="top:56px"><div class="mark dark"><svg width="34" height="34" viewBox="0 0 34 34"><circle cx="17" cy="17" r="17" fill="#fff"/><path d="M10 17.5 L15 22 L24 12.5" stroke="#28222f" stroke-width="3" fill="none"/></svg></div><div class="copy"><h3 class="accent">Principle #1</h3><p>Complete perspective from Executives, Directors, Managers &amp; Staff. Conduct competitive analysis and customer research (optional).</p></div></div>
    <div class="abs principle" style="top:154px"><div class="mark red"><svg width="34" height="34" viewBox="0 0 34 34"><circle cx="17" cy="17" r="17" fill="#fff"/><path d="M10 17.5 L15 22 L24 12.5" stroke="#a8413c" stroke-width="3" fill="none"/></svg></div><div class="copy"><h3>Principle #2</h3><p>Complete perspective from Executives, Directors, Managers &amp; Staff. Conduct competitive analysis and customer research (optional).</p></div></div>
    <div class="abs principle" style="top:252px"><div class="mark dark"><svg width="34" height="34" viewBox="0 0 34 34"><circle cx="17" cy="17" r="17" fill="#fff"/><path d="M10 17.5 L15 22 L24 12.5" stroke="#28222f" stroke-width="3" fill="none"/></svg></div><div class="copy"><h3 class="accent">Principle #3</h3><p>Complete perspective from Executives, Directors, Managers &amp; Staff. Conduct competitive analysis and customer research (optional).</p></div></div>
    <div class="abs principle" style="top:349px"><div class="mark red"><svg width="34" height="34" viewBox="0 0 34 34"><circle cx="17" cy="17" r="17" fill="#fff"/><path d="M10 17.5 L15 22 L24 12.5" stroke="#a8413c" stroke-width="3" fill="none"/></svg></div><div class="copy"><h3>Principle #4</h3><p>Complete perspective from Executives, Directors, Managers &amp; Staff. Conduct competitive analysis and customer research (optional).</p></div></div>
    <div class="abs principle" style="top:447px"><div class="mark dark"><svg width="34" height="34" viewBox="0 0 34 34"><circle cx="17" cy="17" r="17" fill="#fff"/><path d="M10 17.5 L15 22 L24 12.5" stroke="#28222f" stroke-width="3" fill="none"/></svg></div><div class="copy"><h3 class="accent">Principle #5</h3><p>Complete perspective from Executives, Directors, Managers &amp; Staff. Conduct competitive analysis and customer research (optional).</p></div></div>
    <span class="page-no">| Page 5</span>
  </div>
</section>

<section class="slide structure">
  <h2 class="abs display band">Plan Structure</h2>
  <table class="plan">
    <thead>
      <tr><th class="red">Level</th><th class="dark">Planning Element &amp; Definition</th><th class="red">Accountability/Owner</th><th class="dark">Frequency of Modification</th></tr>
    </thead>
    <tbody>
      <tr class="gap"><td colspan="4" style="height:29px"></td></tr>
      <tr class="shade" style="height:60px"><td class="level">1&nbsp; |&nbsp; What (Overall)</td><td>Strategic Priorities</td><td>N/A</td><td>3+ years</td></tr>
      <tr style="height:105px"><td class="level">1.1&nbsp; |&nbsp; What<br>(this year)</td><td>Goals<br>Outcomes &amp; Strategies</td><td>Executive Leadership</td><td>1-3 years</td></tr>
      <tr class="shade" style="height:73px"><td class="level">1.1.1&nbsp; |&nbsp; How</td><td>Key Performance Indicators<br>and/or Initiatives</td><td>N/A</td><td>1 year</td></tr>
      <tr style="height:90px"><td class="level">1.1.1.1&nbsp; |&nbsp; How</td><td>Action Items</td><td></td><td>Quarterly/Monthly</td></tr>
    </tbody>
  </table>
  <span class="page-no">| Page 6</span>
</section>

</body>
</html>
```